Business card for medical clinic

I need an upmarket, modern medical/health business card for my clinic

Contact Information for Business Card

name, address, email, qr code

```html
<!DOCTYPE html>
<html lang="en">
<head>
<meta charset="utf-8">
<title>Meridian Care Clinic – Business Card</title>
<link href="https://fonts.googleapis.com/css2?family=Cinzel:wght@500&family=EB+Garamond:wght@400;500&display=swap" rel="stylesheet">
<style>
  :root {
    --page-bg: #e9e6e1;
    --card-top: #f7f6f3;
    --card-bottom: #e6e4e0;
    --navy: #1b2d4f;
    --navy-deep: #15223f;
    --accent: #1aa6db;
    --brand: #1f3d63;
    --name: #1d5677;
    --muted: #4a4a4a;
    --contact: #d9d2c6;
    --display: "Cinzel", serif;
    --text: "EB Garamond", serif;
  }
  * { margin: 0; padding: 0; box-sizing: border-box; }
  html, body { width: 1200px; height: 1054px; overflow: hidden; }
  body { background: var(--page-bg); position: relative; }

  .card {
    position: absolute;
    left: 100px; top: 225px;
    width: 1000px; height: 604px;
    border-radius: 34px;
    overflow: hidden;
    background: linear-gradient(170deg, var(--card-top) 0%, var(--card-bottom) 100%);
    box-shadow: 0 14px 40px rgba(0,0,0,.18);
  }
  .card__band { position: absolute; inset: 0; width: 100%; height: 100%; }

  .brand {
    position: absolute;
    left: 62px; top: 176px;
    display: flex; align-items: center; gap: 18px;
    font-family: var(--text);
    font-weight: 500;
    font-size: 44px;
    line-height: 1;
    color: var(--brand);
  }
  .brand__square {
    width: 22px; height: 22px;
    background: var(--brand);
    flex: none;
  }

  .person {
    position: absolute;
    right: 48px; top: 74px;
    text-align: right;
  }
  .person__name {
    font-family: var(--display);
    font-weight: 500;
    font-size: 34px;
    letter-spacing: 1px;
    color: var(--name);
    line-height: 1.1;
  }
  .person__role {
    font-family: var(--text);
    font-size: 23px;
    color: var(--muted);
    margin-top: 4px;
  }

  .contact {
    position: absolute;
    right: 48px; top: 408px;
    list-style: none;
    font-family: var(--text);
    font-size: 23px;
    color: var(--contact);
    text-align: right;
  }
  .contact__item {
    display: flex; justify-content: flex-end; align-items: center;
    gap: 16px; height: 37px;
  }
  .contact__icon { width: 22px; height: 22px; flex: none; }
  .contact__item--address { margin-top: 4px; }
</style>
</head>
<body>
  <div class="card">
    <svg class="card__band" viewBox="0 0 1000 604" preserveAspectRatio="none" aria-hidden="true">
      <defs>
        <linearGradient id="bandFill" x1="0" y1="0" x2="1" y2="0">
          <stop offset="0" stop-color="#1f3b60"/>
          <stop offset="1" stop-color="#16233f"/>
        </linearGradient>
      </defs>
      <path class="band-line" d="M0,430 C260,470 520,430 700,340 C820,282 920,270 1000,272" fill="none" stroke="var(--accent)" stroke-width="6"/>
      <path class="band-base" d="M0,470 C260,500 520,460 700,372 C820,315 920,302 1000,304 L1000,604 L0,604 Z" fill="url(#bandFill)"/>
    </svg>

    <div class="brand">
      <span class="brand__square"></span>
      <span class="brand__name">Meridian Care Clinic</span>
    </div>

    <div class="person">
      <div class="person__name">DANIEL HARTLEY</div>
      <div class="person__role">Managing Director</div>
    </div>

    <ul class="contact">
      <li class="contact__item">
        <span>0777-555-01234</span>
        <svg class="contact__icon" viewBox="0 0 24 24" aria-hidden="true"><path fill="var(--accent)" d="M6.6 10.8a15 15 0 0 0 6.6 6.6l2.2-2.2c.3-.3.7-.4 1-.2 1.1.4 2.3.6 3.6.6.6 0 1 .4 1 1V20c0 .6-.4 1-1 1A17 17 0 0 1 3 4c0-.6.4-1 1-1h3.5c.6 0 1 .4 1 1 0 1.3.2 2.5.6 3.6.1.3 0 .7-.2 1z"/></svg>
      </li>
      <li class="contact__item">
        <span>info@meridiancare.com</span>
        <svg class="contact__icon" viewBox="0 0 24 24" aria-hidden="true"><rect x="2" y="5" width="20" height="14" rx="1" fill="var(--accent)"/><path d="M2.5 5.5 12 13l9.5-7.5" fill="none" stroke="#16233f" stroke-width="1.6"/></svg>
      </li>
      <li class="contact__item">
        <span>www.meridiancare.com</span>
        <svg class="contact__icon" viewBox="0 0 24 24" aria-hidden="true"><g fill="none" stroke="var(--accent)" stroke-width="1.8"><circle cx="12" cy="12" r="9"/><ellipse cx="12" cy="12" rx="4" ry="9"/><path d="M3 12h18M5 7h14M5 17h14"/></g></svg>
      </li>
      <li class="contact__item contact__item--address">
        <span>418, Elm Row, Fairview, US 204517</span>
      </li>
    </ul>
  </div>
</body>
</html>
```